Maplecrest Disability - Social Security Disability Attorneys

Our company is expanding to attract clients nationwide for our social security disability practice. We have a logo, but I am looking for a creative and elegant letterhead that projects an image of being technologically advanced but still professional enough for the legal field. I am looking for the "wow factor" combined with this is still professional enough for a law practice.

Requesting letterhead and business card design
Updates

Had to update and change the logo. The previous logo had a typo. Please send updates with the new logo for consideration. The letterhead and business cards should be professional enough to be used for a law firm. Thanks.

Industry/Entity Type

Law Practice, Law Firm, Healthcare Industry, Government

Colors

Designer to choose colors to be used in the design.

Requirements
Nice to have
• **Please create a vertical design for the business card**

```html
<!DOCTYPE html>
<html lang="en">
<head>
<meta charset="UTF-8">
<title>Maplecrest Disability – Business Card</title>
<link href="https://fonts.googleapis.com/css2?family=Cinzel:wght@500;600&family=Montserrat:wght@400;500&display=swap" rel="stylesheet">
<style>
  :root {
    --bg: #d9dadc;
    --card-white: #f7f8f9;
    --brand-blue: #1a63d8;
    --deep-blue: #0f55d6;
    --bright-blue: #1f7fe6;
    --cyan: #14c8f0;
    --orange: #e8720c;
    --text-grey: #4a4d52;
    --rule: #8a8d92;
    --white: #ffffff;
  }
  * { margin: 0; padding: 0; box-sizing: border-box; }
  html, body { width: 1200px; height: 800px; overflow: hidden; }
  body { background: var(--bg); position: relative; font-family: "Montserrat", Arial, sans-serif; }

  .card {
    position: absolute;
    width: 525px; height: 300px;
    border-radius: 22px;
    overflow: hidden;
    box-shadow: 0 14px 30px rgba(0,0,0,0.22);
  }

  /* Front */
  .card-front { left: 60px; top: 110px; background: var(--card-white); }
  .front-waves { position: absolute; inset: 0; }
  .firm-name {
    position: absolute; left: 0; right: 0; top: 32px;
    text-align: center;
    font-family: "Cinzel", Georgia, serif; font-weight: 600;
    font-size: 26px; letter-spacing: 0.5px;
    color: var(--brand-blue);
  }
  .firm-name .mark {
    display: inline-block; width: 10px; height: 10px; border-radius: 50%;
    background: var(--brand-blue); margin-right: 10px; vertical-align: middle;
  }
  .details { position: absolute; left: 40px; top: 88px; display: flex; align-items: stretch; }
  .person { padding-right: 16px; }
  .person-name {
    font-family: "Cinzel", Georgia, serif; font-weight: 600;
    font-size: 18px; color: var(--brand-blue); letter-spacing: 0.3px;
  }
  .person-title { font-size: 12px; color: var(--orange); margin: 2px 0 6px; }
  .address { font-size: 11px; line-height: 1.5; color: var(--text-grey); }
  .divider { width: 1px; background: var(--rule); }
  .contact { list-style: none; padding-left: 14px; }
  .contact li {
    display: flex; align-items: center; gap: 8px;
    font-size: 10.5px; line-height: 17px; color: var(--text-grey);
  }
  .contact svg { width: 11px; height: 11px; flex: none; }

  /* Back */
  .card-back {
    left: 615px; top: 390px;
    background: linear-gradient(150deg, var(--bright-blue) 0%, var(--deep-blue) 55%, #0a4fd0 100%);
  }
  .back-name {
    position: absolute; left: 0; right: 0; top: 56px; text-align: center;
    font-family: "Cinzel", Georgia, serif; font-weight: 500;
    font-size: 32px; color: var(--white); letter-spacing: 0.5px;
  }
  .back-url {
    position: absolute; left: 0; right: 0; top: 104px; text-align: center;
    font-size: 11px; letter-spacing: 5px; color: rgba(255,255,255,0.85);
  }
  .back-art {
    position: absolute; left: 0; right: 0; bottom: 0; height: 150px;
    background: linear-gradient(20deg, var(--cyan) 0%, rgba(31,127,230,0.6) 40%, rgba(15,85,214,0) 80%);
  }
</style>
</head>
<body>

<section class="card card-front" aria-label="Business card front">
  <svg class="front-waves" viewBox="0 0 525 300" preserveAspectRatio="none" aria-hidden="true">
    <path d="M0,268 C300,264 500,220 525,22 L525,300 L0,300 Z" fill="var(--brand-blue)"/>
    <path d="M0,274 C300,270 506,226 525,40" fill="none" stroke="var(--white)" stroke-width="2"/>
    <path d="M130,262 C320,254 490,214 516,0" fill="none" stroke="var(--orange)" stroke-width="4"/>
  </svg>

  <h1 class="firm-name"><span class="mark"></span>Maplecrest Disability</h1>

  <div class="details">
    <div class="person">
      <p class="person-name">Daniel Whitford</p>
      <p class="person-title">Founder &amp; CEO</p>
      <p class="address">4120 Birchwood Lane<br>Juneau, Alaska 99801</p>
    </div>
    <div class="divider"></div>
    <ul class="contact">
      <li>
        <svg viewBox="0 0 12 12"><path d="M2.5 1 L4.5 1 L5.2 3.5 L4 4.4 Q5 6.8 7.6 8 L8.5 6.8 L11 7.5 L11 9.5 Q10.5 11 9 11 Q1 10 1 2.5 Q1.2 1 2.5 1Z" fill="var(--brand-blue)"/></svg>
        555-210-4821
      </li>
      <li>
        <svg viewBox="0 0 12 12"><rect x="3" y="0.8" width="6" height="10.4" rx="1" fill="none" stroke="var(--brand-blue)" stroke-width="1.3"/><circle cx="6" cy="9.3" r="0.7" fill="var(--brand-blue)"/></svg>
        555-318-7702
      </li>
      <li>
        <svg viewBox="0 0 12 12"><rect x="0.8" y="2.2" width="10.4" height="7.6" rx="1" fill="var(--brand-blue)"/><path d="M1.2 2.8 L6 6.5 L10.8 2.8" fill="none" stroke="var(--white)" stroke-width="1"/></svg>
        info@maplecrestdisability.com
      </li>
      <li>
        <svg viewBox="0 0 12 12"><circle cx="6" cy="6" r="5" fill="var(--brand-blue)"/><path d="M1 6 H11 M6 1 Q3 6 6 11 M6 1 Q9 6 6 11" fill="none" stroke="var(--white)" stroke-width="0.8"/></svg>
        maplecrestdisability.com
      </li>
    </ul>
  </div>
</section>

<section class="card card-back" aria-label="Business card back">
  <div class="back-art" role="img" aria-label="Soft light-blue sweeping artwork"></div>
  <h2 class="back-name">Maplecrest Disability</h2>
  <p class="back-url">www.MaplecrestDisability.com</p>
</section>

</body>
</html>
```